Real Estate Company Looking for Business Card Designs for 3 Executives

Hello!
Thanks so much for considering our project! We are a real estate investment company located in Edmonton, Alberta called Bellhaven Group of Companies. We invest/develop both commercial and residential real estate and are looking to create 3 DOUBLE-SIDED business cards for 3 top executives in the company! (for some reason it won't let us select the double-sided option, but yes, the cards are double sided and would be happy to tip extra)

We have certain guidelines that we want our business cards to for sure follow - the back of the Business card has to be the Black Background Version of the Logo which has already been designed and linked as a file (first file). We want the entire back of the card to simply just be the black background logo. In terms of the front of the card, would like to see a smaller version of the white background logo (linked as the second file) in the top left hand corner - of course, feel free to get creative and we can make revisions together along the way! and Then after that, just text. We want the card to be sharp, clean, easy on the eyes and highly professional looking. We would like the card to include the Full name of the Company (Bellhaven Group of Companies), Name of the Person, Title, Phone, Email. If possible please provide the front part of the card for 3 people:

1) Bellhaven Group of Companies, Liora Quenby, Chief Financial Officer, 780-555-0142, lioraquenby@bellhavengroup.example

2) Bellhaven Group of Companies, Tobias Quenby, Chief Executive Officer, 780-555-0187, tobiasquenby@bellhavengroup.example

3) Bellhaven Group of Companies, Rui Delcourt, Chief Operations Officer, 587-555-0163, ruidelcourt@bellhavengroup.example

Thank you so much for considering our project & we look forward to seeing your designs!

```html
<!DOCTYPE html>
<html lang="en">
<head>
<meta charset="utf-8">
<title>Bellhaven Group of Companies – Business Card</title>
<link rel="stylesheet" href="https://fonts.googleapis.com/css2?family=Arimo:wght@400&family=Tinos:wght@700&display=swap">
<style>
  :root {
    --backdrop: #161616;
    --card: #202020;
    --ink: #ffffff;
    --ink-soft: #ececec;
    --rule: #d9d9d9;
  }
  * { box-sizing: border-box; margin: 0; padding: 0; }
  html, body { width: 1200px; height: 1059px; overflow: hidden; }
  body {
    background: var(--backdrop);
    position: relative;
    font-family: "Arimo", Arial, sans-serif;
    color: var(--ink);
  }
  .card {
    position: absolute;
    background: var(--card);
    box-shadow: 0 14px 30px rgba(0,0,0,0.55);
  }
  .card--front { left: 257px; top: 89px; width: 687px; height: 390px; }
  .card--back  { left: 253px; top: 547px; width: 694px; height: 393px; }

  .wordmark {
    font-family: "Arimo", Arial, sans-serif;
    font-weight: 400;
    color: var(--ink);
    text-transform: uppercase;
    text-align: center;
  }
  .wordmark__name { display: block; }
  .wordmark__sub { display: block; }

  .card--front .wordmark {
    position: absolute;
    right: 36px;
    top: 178px;
    width: 200px;
  }
  .card--front .wordmark__name { font-size: 19px; letter-spacing: 5px; }
  .card--front .wordmark__sub { font-size: 8px; letter-spacing: 2.2px; margin-top: 6px; }

  .identity { position: absolute; left: 35px; top: 180px; }
  .identity__name {
    font-family: "Tinos", "Times New Roman", serif;
    font-weight: 700;
    font-size: 28px;
    letter-spacing: 0.5px;
    text-transform: uppercase;
    line-height: 1;
  }
  .identity__title { font-size: 17.5px; color: var(--ink-soft); margin-top: 8px; }

  .divider {
    position: absolute;
    left: 35px; right: 36px; top: 254px;
    height: 1px;
    background: var(--rule);
  }

  .contacts { position: absolute; left: 35px; top: 277px; list-style: none; }
  .contacts li {
    display: flex;
    align-items: center;
    font-size: 17px;
    height: 27.5px;
    color: var(--ink-soft);
  }
  .contacts svg { width: 15px; height: 15px; margin-right: 6px; fill: var(--ink); flex: none; }

  .card--back .wordmark {
    position: absolute;
    left: 0; right: 0;
    top: 150px;
  }
  .card--back .wordmark__name { font-size: 30px; letter-spacing: 12px; padding-left: 12px; }
  .card--back .wordmark__sub { font-size: 11px; letter-spacing: 3.5px; margin-top: 12px; }
</style>
</head>
<body>

  <section class="card card--front" aria-label="Card front">
    <div class="wordmark">
      <span class="wordmark__name">Bellhaven</span>
      <span class="wordmark__sub">Group of Companies</span>
    </div>

    <div class="identity">
      <h1 class="identity__name">Liora Quenby</h1>
      <p class="identity__title">Chief Financial Officer</p>
    </div>

    <div class="divider"></div>

    <ul class="contacts">
      <li>
        <svg viewBox="0 0 24 24" aria-hidden="true"><path d="M6.6 10.8a15.1 15.1 0 0 0 6.6 6.6l2.2-2.2a1 1 0 0 1 1-.25 11.4 11.4 0 0 0 3.6.57 1 1 0 0 1 1 1V20a1 1 0 0 1-1 1A17 17 0 0 1 3 4a1 1 0 0 1 1-1h3.5a1 1 0 0 1 1 1c0 1.25.2 2.45.57 3.57a1 1 0 0 1-.25 1z"/></svg>
        780-555-0142
      </li>
      <li>
        <svg viewBox="0 0 24 24" aria-hidden="true"><path d="M2 5h20v14H2z M3.5 6.5v.4L12 13l8.5-6.1v-.4z" fill-rule="evenodd"/></svg>
        lioraquenby@bellhavengroup.example
      </li>
      <li>
        <svg viewBox="0 0 24 24" aria-hidden="true"><circle cx="12" cy="12" r="10"/><path d="M7 7c2 0 3 1 3 3s-2 2-2 4 1 3 0 4c-2-1-4-3-4-6 0-2 1-4 3-5zM15 5c2 1 4 3 4 6-1 0-2 1-2 2s-1 2-2 2-1-2-1-3-2-1-2-3 2-2 3-4z" fill="#202020"/></svg>
        www.bellhavengroup.example
      </li>
    </ul>
  </section>

  <section class="card card--back" aria-label="Card back">
    <div class="wordmark">
      <span class="wordmark__name">Bellhaven</span>
      <span class="wordmark__sub">Group of Companies</span>
    </div>
  </section>

</body>
</html>
```